Moravel Aesthetic Doctor

I require an elegant, luxurious looking business card for my aesthetic business. I am a doctor and that will set me aside from competitors. I am planning to provide home and spa based treatments to clients with high expectations. I have attached my logo.

```html
<!DOCTYPE html>
<html lang="en">
<head>
<meta charset="utf-8">
<title>Moravel Aesthetic Doctor – Business Card</title>
<link href="https://fonts.googleapis.com/css2?family=Roboto:wght@300;400;500&display=swap" rel="stylesheet">
<style>
  :root {
    --backdrop: #d9d9d9;
    --card-white: #ffffff;
    --sky: #5ec3ee;
    --sky-pale: #aee1f5;
    --slate: #a7a9ac;
    --ink-grey: #8a8c8f;
    --mist: #e6eef6;
    --white: #ffffff;
  }
  * { box-sizing: border-box; margin: 0; padding: 0; }
  html, body { width: 1125px; height: 1200px; overflow: hidden; }
  body {
    background: var(--backdrop);
    font-family: "Roboto", Arial, sans-serif;
    position: relative;
  }
  .card {
    position: absolute;
    left: 150px;
    width: 825px;
    height: 470px;
    border-radius: 26px;
    overflow: hidden;
    box-shadow: 0 4px 8px rgba(0,0,0,0.25);
  }
  .card--front { top: 98px; background: var(--card-white); }
  .card--back {
    top: 632px;
    background: linear-gradient(180deg, var(--sky-pale) 0%, #b7cdd8 22%, var(--slate) 55%, #b3c9d4 82%, var(--sky-pale) 100%);
  }
  .card svg { position: absolute; left: 0; top: 0; }

  .motif-front {
    position: absolute; left: 300px; top: 30px; width: 460px; height: 400px;
    border-radius: 50%;
    background: radial-gradient(ellipse at 60% 45%, rgba(200,220,240,0.55), rgba(230,238,246,0.25) 55%, rgba(255,255,255,0) 72%);
  }
  .wordmark {
    position: absolute; left: 50px; top: 38px;
    color: var(--ink-grey); font-weight: 300; line-height: 1;
  }
  .wordmark__name { font-size: 62px; letter-spacing: 2px; display: block; }
  .wordmark__line { font-size: 26px; letter-spacing: 2px; display: block; margin-top: 4px; }

  .person { position: absolute; left: 50px; top: 200px; }
  .person__name { font-size: 31px; font-weight: 500; color: var(--sky); }
  .person__name small { font-size: 19px; font-weight: 400; margin-left: 4px; }
  .person__title { font-size: 21px; font-weight: 300; color: var(--ink-grey); margin-top: 8px; }

  .contacts { position: absolute; left: 50px; top: 290px; list-style: none; }
  .contacts li {
    display: flex; align-items: center; height: 33px;
    font-size: 21px; font-weight: 300; color: var(--ink-grey);
  }
  .contacts svg { position: static; width: 20px; height: 20px; margin-right: 14px; }
  .contacts .accent { color: var(--sky); }
  .social { position: absolute; left: 304px; top: 364px; display: flex; gap: 20px; }
  .social span { width: 27px; height: 27px; border-radius: 50%; background: var(--sky); display: block; }

  .motif-back {
    position: absolute; left: 330px; top: 20px; width: 440px; height: 420px; border-radius: 50%;
    background: radial-gradient(ellipse at 55% 50%, rgba(255,255,255,0.18), rgba(255,255,255,0.06) 60%, rgba(255,255,255,0) 72%);
  }
  .brand-back {
    position: absolute; left: 155px; top: 128px; display: flex; align-items: center; gap: 24px;
  }
  .brand-back__dot { width: 140px; height: 140px; border-radius: 50%; border: 4px solid var(--white); }
  .brand-back__text { color: var(--white); font-weight: 300; line-height: 1; }
  .brand-back__text .wordmark__name { font-size: 86px; letter-spacing: 3px; }
  .brand-back__text .wordmark__line { font-size: 34px; letter-spacing: 3px; margin-top: 6px; }

  .services {
    position: absolute; left: 0; right: 0; top: 318px; text-align: center;
    color: var(--white); font-size: 22px; font-weight: 300; line-height: 33px;
  }
</style>
</head>
<body>

<section class="card card--front">
  <div class="motif-front" role="img" aria-label="Faint decorative brand motif of flowing hair lines"></div>
  <svg width="825" height="470" viewBox="0 0 825 470" aria-hidden="true">
    <circle cx="620" cy="230" r="205" fill="none" stroke="#eeeeee" stroke-width="8"/>
    <path d="M0 415 C 120 395, 230 400, 330 425 C 470 455, 650 450, 825 425 L825 470 L0 470 Z" fill="var(--slate)"/>
    <path d="M0 412 C 110 390, 200 395, 280 418 C 200 402, 100 405, 0 422 Z" fill="var(--sky)"/>
    <path d="M560 448 C 660 446, 750 438, 825 420 L825 430 C 750 446, 660 452, 560 448 Z" fill="var(--sky)"/>
  </svg>
  <div class="wordmark">
    <span class="wordmark__name">MORAVEL</span>
    <span class="wordmark__line">AESTHETIC DOCTOR</span>
  </div>
  <div class="person">
    <p class="person__name">Dr Elsa Vantry, <small>MRCPCH MD</small></p>
    <p class="person__title">Australasian Diploma of Aesthetic Medicine</p>
  </div>
  <ul class="contacts">
    <li><svg viewBox="0 0 20 20"><path d="M4 2 L8 2 L9 6 L7 8 C8 11 9 12 12 13 L14 11 L18 12 L18 16 C18 17 17 18 16 18 C8 18 2 12 2 4 C2 3 3 2 4 2 Z" fill="var(--sky)"/></svg>0800 555 014</li>
    <li><svg viewBox="0 0 20 20"><rect x="2" y="5" width="16" height="11" rx="1" fill="none" stroke="var(--sky)" stroke-width="1.6"/><path d="M2 5 L10 11 L18 5" fill="none" stroke="var(--sky)" stroke-width="1.6"/></svg>elsa@moravel.co.nz</li>
    <li><svg viewBox="0 0 20 20"><circle cx="10" cy="10" r="8" fill="none" stroke="var(--sky)" stroke-width="1.5"/><ellipse cx="10" cy="10" rx="3.5" ry="8" fill="none" stroke="var(--sky)" stroke-width="1.3"/><path d="M2 10 H18 M3.5 6 H16.5 M3.5 14 H16.5" stroke="var(--sky)" stroke-width="1.2"/></svg>www.<span class="accent">moravel</span>.co.nz</li>
  </ul>
  <div class="social"><span></span><span></span></div>
</section>

<section class="card card--back">
  <div class="motif-back" role="img" aria-label="Faint decorative brand motif of flowing hair lines"></div>
  <svg width="825" height="470" viewBox="0 0 825 470" aria-hidden="true">
    <circle cx="560" cy="225" r="215" fill="none" stroke="rgba(255,255,255,0.18)" stroke-width="8"/>
  </svg>
  <div class="brand-back">
    <span class="brand-back__dot"></span>
    <div class="brand-back__text">
      <span class="wordmark__name">MORAVEL</span>
      <span class="wordmark__line">AESTHETIC DOCTOR</span>
    </div>
  </div>
  <div class="services">
    <p>Dermal injectables • Plasma facials • Microneedling</p>
    <p>Skin boosters • Excessive sweating</p>
    <p>Home and Spa Based Treatments</p>
  </div>
</section>

</body>
</html>
```